Business Card for my New Brokerage

Looking to get a business card design for my new Real Estate Brokerage.
I want it with Picture, Phone Number, Email, Website, Office Address
Name and Designation. Please add logo too.

Target Market(s)

Real Estate Investors or Home Buyers

Industry/Entity Type

Real Estate

Contact Information for Business Card

Name, Email, Phone Number, website, email, office address

Colors
EB3D1F
EC4F4E
F09395
F8D3D4
FCEDEE

Requirements
Must have
• Minimalistic, Clean, Modern, Photo
Nice to have
• White and Red Colors

```html
<!DOCTYPE html>
<html lang="en">
<head>
<meta charset="utf-8">
<title>Ember Realty Inc — Business Card</title>
<link href="https://fonts.googleapis.com/css2?family=Montserrat:wght@400;500;700;800&display=swap" rel="stylesheet">
<style>
  :root {
    --page-bg: #e9e9e9;
    --card-dark: #1f1f20;
    --brand-red: #e00000;
    --accent-gold: #d4b15f;
    --text-light: #ffffff;
    --photo-top: #e7e4e1;
    --photo-bottom: #2a3345;
  }
  * { box-sizing: border-box; margin: 0; padding: 0; }
  html, body {
    width: 1200px; height: 900px; overflow: hidden;
    background: var(--page-bg);
    font-family: "Montserrat", sans-serif;
  }
  .business-card {
    position: absolute; left: 100px; top: 165px;
    width: 1000px; height: 570px;
    border-radius: 34px; overflow: hidden;
    background: var(--card-dark);
    box-shadow: 0 18px 40px rgba(0,0,0,.25);
  }
  .card-wave { position: absolute; inset: 0; }
  .brand-name {
    position: absolute; left: 150px; top: 60px;
    color: var(--brand-red);
    font-weight: 800; font-size: 44px; letter-spacing: 1px;
    line-height: 1; white-space: nowrap;
  }
  .agent-photo {
    position: absolute; left: 660px; top: 150px;
    width: 250px; height: 250px; border-radius: 50%;
    border: 4px solid var(--brand-red);
    background: linear-gradient(180deg, var(--photo-top) 0%, var(--photo-top) 55%, var(--photo-bottom) 100%);
  }
  .office-address {
    position: absolute; left: 50px; top: 440px;
    color: var(--text-light); font-weight: 500; font-size: 21px; line-height: 1.35;
    white-space: nowrap;
  }
  .agent-details {
    position: absolute; right: 330px; top: 370px;
    text-align: right; color: var(--text-light); white-space: nowrap;
  }
  .agent-name { font-weight: 800; font-size: 32px; letter-spacing: 1px; line-height: 1.2; }
  .agent-title { font-weight: 500; font-size: 22px; margin-top: 2px; }
  .contact-list { list-style: none; margin-top: 10px; font-size: 20px; font-weight: 400; line-height: 1.4; }
  .contact-list li { display: flex; justify-content: flex-end; align-items: center; gap: 10px; }
  .contact-icon { width: 17px; height: 17px; fill: none; stroke: var(--text-light); stroke-width: 2; }
</style>
</head>
<body>
  <div class="business-card">
    <svg class="card-wave" viewBox="0 0 1000 570" preserveAspectRatio="none" aria-hidden="true">
      <path d="M0,95 C40,260 230,335 520,340 C740,344 900,370 1000,470 L1000,570 L0,570 Z" fill="var(--brand-red)"/>
      <path d="M0,150 C60,285 250,330 520,332 C740,336 905,362 1000,455" fill="none" stroke="var(--card-dark)" stroke-width="10"/>
      <path d="M0,135 C60,275 250,322 520,324 C740,328 905,354 1000,447" fill="none" stroke="var(--accent-gold)" stroke-width="7"/>
    </svg>

    <div class="brand-name">EMBER REALTY INC</div>

    <div class="agent-photo" role="img" aria-label="Portrait photo of the agent"></div>

    <p class="office-address">1870 Maple Ridge Court<br>Fairview, GA 30214</p>

    <div class="agent-details">
      <h1 class="agent-name">DANIEL REYES</h1>
      <p class="agent-title">Founder and President</p>
      <ul class="contact-list">
        <li>+330 555-0142
          <svg class="contact-icon" viewBox="0 0 24 24"><path d="M5 3h4l2 5-3 2a12 12 0 0 0 6 6l2-3 5 2v4a2 2 0 0 1-2 2A18 18 0 0 1 3 5a2 2 0 0 1 2-2z"/></svg>
        </li>
        <li>info@emberrealtyinc.com
          <svg class="contact-icon" viewBox="0 0 24 24"><rect x="3" y="5" width="18" height="14" rx="1"/><path d="M3 6l9 7 9-7"/></svg>
        </li>
        <li>www.emberrealtyinc.com
          <svg class="contact-icon" viewBox="0 0 24 24"><circle cx="12" cy="12" r="9"/><path d="M3 12h18M12 3c3 3 3 15 0 18M12 3c-3 3-3 15 0 18"/></svg>
        </li>
      </ul>
    </div>
  </div>
</body>
</html>
```